Awesome photographers card for an awesome new business

Double sided business card Black background and silver logo in middle on one side. Details on otherside. please keep it simple

Industry/Entity Type

Photographer

Contact Information for Business Card

Gerald Fenwick
0452817360
GeraldFenwickPhotography47@mailbox.test
www.GeraldFenwickPhotography.test.au
Instagram _Gerald_fenwick

Requirements
Must have
• My logo in Silver
• please use instagram logo instead of "Instagram"

```html
<!DOCTYPE html>
<html lang="en">
<head>
<meta charset="utf-8">
<title>Gerald Fenwick Photography – Business Card</title>
<link rel="stylesheet" href="https://fonts.googleapis.com/css2?family=Open+Sans:wght@400;600;700&display=swap">
<style>
  :root {
    --page-bg: #ececea;
    --card-black: #0b0b0b;
    --card-black-soft: #1c1c1c;
    --silver: #c9cacc;
    --band-grey: #9a9ea1;
    --stripe-white: #e9e9e9;
    --text-white: #ffffff;
    --text-dark: #2a2a2a;
  }
  * { box-sizing: border-box; margin: 0; padding: 0; }
  html, body {
    width: 1200px; height: 900px; overflow: hidden;
    background: var(--page-bg);
    font-family: "Open Sans", Arial, sans-serif;
  }
  .sheet {
    width: 1200px; height: 900px;
    display: flex; align-items: center; justify-content: center; gap: 40px;
  }
  .card {
    position: relative;
    width: 540px; height: 320px;
    overflow: hidden;
    box-shadow: 0 8px 24px rgba(0,0,0,0.18);
  }
  .card--front { background: var(--card-black); }
  .card--back {
    background: radial-gradient(ellipse at 45% 35%, var(--card-black-soft), var(--card-black) 75%);
  }
  .brand-mark {
    position: absolute;
    display: flex; align-items: center; gap: 12px;
    color: var(--silver);
    font-weight: 600;
    letter-spacing: 0.14em;
    text-transform: uppercase;
    line-height: 1.35;
  }
  .brand-mark__dot {
    flex: none;
    border: 2px solid var(--silver);
    border-radius: 50%;
  }
  .card--front .brand-mark {
    left: 50%; top: 50%; transform: translate(-50%, -50%);
    font-size: 13px;
  }
  .card--front .brand-mark__dot { width: 46px; height: 46px; }
  .card--back .brand-mark {
    right: 26px; top: 40px;
    font-size: 10px;
  }
  .card--back .brand-mark__dot { width: 34px; height: 34px; }
  .swoosh { position: absolute; inset: 0; width: 100%; height: 100%; }
  .holder-name {
    position: absolute; left: 34px; top: 58px;
    color: var(--text-white);
    font-weight: 700; font-size: 19px;
    text-transform: uppercase; letter-spacing: 0.01em;
  }
  .contact-list {
    position: absolute; left: 34px; top: 150px;
    list-style: none;
    color: var(--text-white);
    font-size: 13px; line-height: 19px;
  }
  .contact-list li { display: flex; align-items: center; gap: 7px; }
  .contact-list svg { width: 11px; height: 11px; flex: none; }
  .social-handle {
    position: absolute; right: 24px; top: 138px;
    display: flex; align-items: center; gap: 6px;
    color: var(--text-dark); font-size: 12px;
  }
  .social-handle__square {
    width: 11px; height: 11px; background: var(--text-dark);
  }
</style>
</head>
<body>
<main class="sheet">
  <section class="card card--front" aria-label="Card front">
    <div class="brand-mark">
      <span class="brand-mark__dot"></span>
      <span>Gerald Fenwick<br>Photography</span>
    </div>
  </section>

  <section class="card card--back" aria-label="Card back">
    <svg class="swoosh" viewBox="0 0 540 320" preserveAspectRatio="none" aria-hidden="true">
      <path d="M0,320 L0,292 C160,300 300,262 385,178 C425,140 470,128 540,124 L540,320 Z" fill="var(--band-grey)"/>
      <path d="M0,280 C150,288 290,250 372,172 C300,246 160,282 0,272 Z" fill="var(--stripe-white)"/>
      <path d="M0,286 C155,294 296,256 380,176" fill="none" stroke="#000" stroke-width="3"/>
    </svg>

    <h1 class="holder-name">Gerald Fenwick</h1>

    <div class="brand-mark">
      <span class="brand-mark__dot"></span>
      <span>Gerald Fenwick<br>Photography</span>
    </div>

    <ul class="contact-list">
      <li>
        <svg viewBox="0 0 12 12"><path d="M2.5 1 L4.5 1 L5.2 3.6 L3.9 4.6 C4.5 6 5.9 7.5 7.4 8.1 L8.4 6.8 L11 7.5 L11 9.5 C11 10.3 10.3 11 9.5 11 C5 11 1 7 1 2.5 C1 1.7 1.7 1 2.5 1 Z" fill="#fff"/></svg>
        <span>0452817360</span>
      </li>
      <li>
        <svg viewBox="0 0 12 12"><rect x="0.5" y="2" width="11" height="8" fill="#fff"/><path d="M0.5 2 L6 6.5 L11.5 2" fill="none" stroke="#111" stroke-width="1"/></svg>
        <span>GeraldFenwickPhotography47@mailbox.test</span>
      </li>
      <li>
        <svg viewBox="0 0 12 12"><circle cx="6" cy="6" r="5.5" fill="#fff"/><path d="M1 6 H11 M6 0.5 C3.5 3 3.5 9 6 11.5 M6 0.5 C8.5 3 8.5 9 6 11.5" fill="none" stroke="#111" stroke-width="0.8"/></svg>
        <span>www.GeraldFenwickPhotography.test.au</span>
      </li>
    </ul>

    <div class="social-handle">
      <span class="social-handle__square"></span>
      <span>_Gerald_fenwick</span>
    </div>
  </section>
</main>
</body>
</html>
```